Verodex business card

Business card for sustainable investment company called "Verodex". Verodex is an exchange platform selling carbon credits between buyers and sellers. Carbon Credits are an environmental commodity for reducing global carbon emissions.

the card should obviously have our logo and the theme should be sustainability/environment mixed with a trading platform.

Contact Information for Business Card

Logo, Name, Title, Phone, Email

Colors
0054AA
0677BA
7BADD7
CADEEF
E8F1F8
0094D4
00A9DD
6FCCEA
C7EBF8
E9F6FB
00AB8E
00BBA5
67D7C9
C6EFE9
E9F9F6
59FF00
82FF00
B8FF75
E3FFCB
F4FFEA

```html
<!DOCTYPE html>
<html lang="en">
<head>
<meta charset="utf-8">
<title>Verodex business card</title>
<link href="https://fonts.googleapis.com/css2?family=Montserrat:wght@400;500;600;700&display=swap" rel="stylesheet">
<style>
  :root {
    --page-bg: #e4e6ea;
    --navy: #1b2a47;
    --cyan: #2ebde9;
    --aqua: #5ccbdc;
    --royal: #3f6cb8;
    --white: #ffffff;
    --ink: #1e2433;
  }
  * { box-sizing: border-box; margin: 0; padding: 0; }
  html, body {
    width: 1200px; height: 900px; overflow: hidden;
    background: var(--page-bg);
    font-family: "Montserrat", sans-serif;
  }
  .sheet {
    width: 1200px; height: 900px;
    display: flex; flex-direction: column;
    align-items: center; justify-content: center; gap: 40px;
  }
  .card {
    position: relative; width: 700px; height: 400px; overflow: hidden;
    box-shadow: 0 8px 24px rgba(0,0,0,.18);
  }

  /* front */
  .card-front {
    background: linear-gradient(30deg, var(--aqua) 0%, var(--cyan) 40%, var(--royal) 100%);
    display: flex; align-items: center; justify-content: center;
  }
  .brand { display: flex; align-items: center; gap: 18px; }
  .brand-dot { width: 44px; height: 44px; background: var(--white); }
  .brand-name {
    font-weight: 600; font-size: 66px; letter-spacing: 3px;
    color: var(--white); text-transform: uppercase; line-height: 1;
  }

  /* back */
  .card-back { background: var(--white); }
  .wave { position: absolute; inset: 0; width: 700px; height: 400px; }
  .back-brand { position: absolute; left: 58px; top: 90px; gap: 14px; z-index: 1; }
  .back-brand .brand-dot { width: 34px; height: 34px; background: var(--cyan); }
  .back-brand .brand-name { font-size: 42px; color: var(--navy); letter-spacing: 2px; }

  .person { position: absolute; right: 60px; top: 104px; text-align: right; z-index: 1; }
  .person-name {
    font-weight: 700; font-size: 28px; letter-spacing: 1px; text-transform: uppercase; line-height: 1.2;
  }
  .person-first { color: var(--navy); }
  .person-last { color: var(--cyan); }
  .person-title { font-weight: 500; font-size: 17px; color: var(--ink); margin-top: 4px; }

  .contacts {
    position: absolute; left: 100px; top: 188px; list-style: none; z-index: 1;
    display: flex; flex-direction: column; gap: 6px;
  }
  .contact { display: flex; align-items: center; gap: 12px; font-size: 19px; line-height: 24px; color: var(--ink); font-weight: 500; }
  .contact svg { width: 20px; height: 20px; flex: none; }
</style>
</head>
<body>
<main class="sheet">
  <section class="card card-front" aria-label="Card front">
    <div class="brand">
      <span class="brand-dot"></span>
      <span class="brand-name">Verodex</span>
    </div>
  </section>

  <section class="card card-back" aria-label="Card back">
    <svg class="wave" viewBox="0 0 700 400" aria-hidden="true">
      <defs>
        <linearGradient id="waveFill" x1="0" y1="1" x2="1" y2="0">
          <stop offset="0" stop-color="#5ccbdc"/>
          <stop offset="0.45" stop-color="#2ebde9"/>
          <stop offset="1" stop-color="#3f6cb8"/>
        </linearGradient>
      </defs>
      <path d="M0,400 L0,386 C120,332 250,336 400,310 C550,284 660,250 700,138 L700,400 Z" fill="url(#waveFill)"/>
      <path d="M0,374 C120,320 250,324 400,298 C550,272 650,238 690,122" fill="none" stroke="#1b2a47" stroke-width="4"/>
    </svg>

    <div class="brand back-brand">
      <span class="brand-dot"></span>
      <span class="brand-name">Verodex</span>
    </div>

    <div class="person">
      <p class="person-name"><span class="person-first">Elias</span> <span class="person-last">Varden</span></p>
      <p class="person-title">Co-Founder</p>
    </div>

    <ul class="contacts">
      <li class="contact">
        <svg viewBox="0 0 24 24"><path fill="#2ebde9" d="M6.6 10.8a15 15 0 0 0 6.6 6.6l2.2-2.2c.3-.3.7-.4 1-.2 1.1.4 2.300.6 3.6.6.6 0 1 .4 1 1V20c0 .6-.4 1-1 1A17 17 0 0 1 3 4c0-.6.4-1 1-1h3.5c.6 0 1 .4 1 1 0 1.3.2 2.5.6 3.6.1.3 0 .7-.2 1z"/></svg>
        <span>308-555-0147</span>
      </li>
      <li class="contact">
        <svg viewBox="0 0 24 24"><rect x="2" y="5" width="20" height="14" rx="1" fill="#2ebde9"/><path d="M2 6l10 7 10-7" fill="none" stroke="#fff" stroke-width="1.6"/></svg>
        <span>info@verodex.com</span>
      </li>
      <li class="contact">
        <svg viewBox="0 0 24 24"><circle cx="12" cy="12" r="10" fill="#2ebde9"/><path d="M2 12h20M12 2c3 3 3 17 0 20M12 2c-3 3-3 17 0 20" fill="none" stroke="#fff" stroke-width="1.3"/></svg>
        <span>www.verodex.com</span>
      </li>
    </ul>
  </section>
</main>
</body>
</html>
```